Quill Harbor (IT/Network Services)

Quill Harbor, LLC provides technology services to small and medium businesses. Essentially, anytime you've every thought your business might need an "IT guy" to handle something you could instead call us to handle it. Basically, you can outsource your IT needs to us.

This is a brand new company and so we'll need a brand new website. I'd like to use WordPress to handle the site since that will make things easier for me to maintain in the long run.

The site should include a, more-or-less, static front page with the dynamic data occurring on pages linked from a navigational area.

I have a logo already designed that I would like to see used in the design. The one with "white" in the title is the official logo, just added some other versions for your perusal.

Color queues from the logo but feel free to add other colors where applicable.

The site should feel somewhat corporate but with a "younger" slant (something a 25-35 year old would enjoy).

Pages (either to be added initially or by me after design completion):
"About" section - includes company history, business philosophy, etc.
"Services" section - service options, service approach, service specifics
"Testimonials" section - (eventually)
"News" section - (eventually) industry news, company news, events, blog
Contact Links

Websites to view:
The two largest local competitors:
http://www.brightmarsh-tech.example/
http://www.kelvarworks.example/
Other local competitors:
http://www.tpbllc.example/
http://www.morrowfield.example/

Other info you might find useful:
Domain: qhllc.example
Address:
417 Elm Row S
Suite 512B
Nashville, TN 37288
Phone: 615-555-0187
Emails available for use/display:
info@qhllc.example
sales@qhllc.example

Target Market(s)

Our target clients are mainly small businesses (25 or less computer users) which means we're looking at a lot of start-ups or younger companies. We'll be interacting with many entrepreneurs and young business owners.

Requirements
Must have
• Need full WP theme (not a mockup)

```html
<!DOCTYPE html>
<html lang="en">
<head>
<meta charset="utf-8">
<title>Quill Harbor — IT &amp; Network Services</title>
<link rel="stylesheet" href="https://fonts.googleapis.com/css2?family=Arimo:ital,wght@0,400;0,700;1,400&family=Questrial&family=Ubuntu:wght@400;500&display=swap">
<style>
:root{
  --outer:#efeff1;
  --topbar:#3b3b3d;
  --topbar-side:#707072;
  --page:#ffffff;
  --ink:#111111;
  --text:#666666;
  --muted:#8a8a8a;
  --orange:#f0940e;
  --nav:#3e3e40;
  --rule:#d6d6d6;
  --button:#dcdcdc;
  --footer:#d8d8d8;
  --badge:#3a3a3a;
  --phone:#ee1c4a;
}
*{margin:0;padding:0;box-sizing:border-box}
html,body{width:1098px;height:1200px;overflow:hidden;background:var(--outer)}
body{position:relative;font-family:"Arimo",Arial,sans-serif;color:var(--text)}
a{color:inherit;text-decoration:none}
.abs{position:absolute}

.top-strip{left:0;top:0;width:1098px;height:17px;background:var(--topbar-side)}
.top-strip::after{content:"";position:absolute;left:72px;top:0;width:955px;height:17px;background:var(--topbar)}
.page{left:72px;top:17px;width:955px;height:970px;background:var(--page)}

.brand{left:103px;top:58px;display:flex;align-items:center;gap:12px}
.brand-dot{width:34px;height:34px;border-radius:50%;background:var(--orange)}
.brand-name{font-family:"Ubuntu",sans-serif;font-weight:400;font-size:30px;letter-spacing:1px;color:#6d6d6d}

.account-links{right:89px;top:51px;font-family:"Ubuntu",sans-serif;font-size:12.5px;color:var(--ink);word-spacing:1px}
.account-links span{margin:0 6px}
.social-title{right:89px;top:83px;font-family:"Ubuntu",sans-serif;font-weight:500;font-size:12.5px;color:var(--ink)}
.social-icon{top:102px;width:40px;height:40px;border-radius:6px}
.social-icon.one{left:918px;background:#3b5a9a}
.social-icon.two{left:967px;background:#4bb7e2}

.main-nav{left:89px;top:162px;width:920px;height:63px;background:var(--nav)}
.nav-home{left:0;top:0;width:59px;height:63px;background:var(--orange);display:flex;align-items:center;justify-content:center}
.nav-item{top:0;height:63px;line-height:63px;font-family:"Ubuntu",sans-serif;font-size:17px;color:var(--orange)}
.nav-sep{top:10px;height:43px;border-left:1px dotted #6a6a6c}

.hero{left:88px;top:233px;width:921px;height:319px;background:
  linear-gradient(160deg,rgba(255,240,220,.35) 0%,rgba(0,0,0,0) 40%),
  radial-gradient(ellipse at 40% 50%,#c9915e 0%,#a46a3c 45%,#6d4425 100%)}
.hero-title{left:552px;top:416px;width:457px;height:45px;background:#3a3230;color:#fff;font-family:"Ubuntu",sans-serif;font-size:32px;text-align:right;padding-right:20px;line-height:45px}
.hero-sub{left:614px;top:465px;width:395px;height:43px;background:rgba(255,244,232,.88);color:var(--orange);font-family:"Ubuntu",sans-serif;font-size:32px;text-align:right;padding-right:20px;line-height:43px}
.slider-controls{left:775px;top:512px}

.section-title{top:576px;font-family:"Questrial",sans-serif;font-size:20.5px;color:var(--ink);letter-spacing:.3px}
.col-rule{top:576px;height:377px;border-left:1px solid var(--rule)}

.welcome-photo{left:89px;top:632px;width:371px;height:151px;background:linear-gradient(90deg,#dfe6e4 0%,#b9c4bd 40%,#4a4c4e 70%,#e8ecec 100%)}
.welcome-lead{left:89px;top:805px;font-size:13.5px;font-weight:700;color:var(--ink)}
.welcome-body{left:89px;top:824px;width:360px;font-size:13.5px;line-height:19.6px;color:var(--text)}

.read-more{top:915px;width:99px;height:28px;border-radius:7px;background:var(--button);font-size:13px;color:#333;text-align:center;line-height:28px}

.news-item{left:537px;width:225px;height:60px}
.date-badge{left:0;top:0;width:50px;height:51px;border-radius:7px;background:var(--badge);color:#fff;font-size:20px;text-align:center;line-height:55px;box-shadow:inset 0 6px 0 #2a2a2a}
.news-date{left:65px;top:-2px;font-size:12.5px;color:var(--ink);text-decoration:underline}
.news-text{left:65px;top:18px;width:170px;font-size:11.5px;line-height:19.6px;color:var(--ink)}

.quote{left:804px;width:205px}
.quote-mark{left:0;top:2px;width:16px;height:16px;border-radius:50%;background:#ececec;display:flex;align-items:center;justify-content:center}
.quote-text{left:22px;top:-4px;width:183px;font-size:12.5px;line-height:19.6px;color:var(--ink)}
.quote-name{right:0;top:55px;font-size:12.5px;font-style:italic;color:var(--orange)}

.footer{left:72px;top:987px;width:955px;height:213px;background:var(--footer)}
.footer-title{top:1024px;font-family:"Arimo",sans-serif;font-size:19px;color:var(--ink)}
.footer-list{top:1062px;list-style:none;font-size:13px;line-height:21.5px;color:#777}
.footer-list li::before{content:"";display:inline-block;margin-right:6px;vertical-align:1px;border-left:4px solid #777;border-top:3px solid transparent;border-bottom:3px solid transparent}
.call-title{left:442px;top:1026px;font-size:19.5px;color:var(--ink)}
.phone-icon{left:441px;top:1067px;width:38px;height:38px;border-radius:5px;background:var(--phone);display:flex;align-items:center;justify-content:center}
.phone-number{left:486px;top:1073px;font-size:22px;color:#444}
.footer-brand{left:752px;top:1100px;display:flex;align-items:center;gap:12px}
.footer-brand .brand-dot{background:#8a8a8a}
.footer-brand .brand-name{color:#7a7a7a}
.copyright{left:117px;top:1172px;font-size:11px;color:#a2a2a2}
</style>
</head>
<body>
<div class="abs top-strip"></div>
<div class="abs page"></div>

<header>
  <a class="abs brand" href="#"><span class="brand-dot"></span><span class="brand-name">QUILL HARBOR</span></a>
  <div class="abs account-links">NEW USER?<span>|</span>REGISTRATION<span>|</span>SIGN IN<span>|</span>HELP</div>
  <div class="abs social-title">SOCIALIZE WITH US</div>
  <a class="abs social-icon one" href="#" aria-label="Social network profile"></a>
  <a class="abs social-icon two" href="#" aria-label="Social network profile"></a>

  <nav class="abs main-nav">
    <a class="abs nav-home" href="#" aria-label="Home">
      <svg width="22" height="20" viewBox="0 0 22 20"><path d="M2 10 L11 2 L20 10 M5 8 V18 H17 V8" fill="none" stroke="#fff" stroke-width="1.8" stroke-linejoin="round"/><rect x="9" y="12" width="4" height="6" fill="#fff"/></svg>
    </a>
    <a class="abs nav-item" style="left:81px" href="#">ABOUT US</a>
    <span class="abs nav-sep" style="left:181px"></span>
    <a class="abs nav-item" style="left:203px" href="#">SOLUTIONS</a>
    <span class="abs nav-sep" style="left:308px"></span>
    <a class="abs nav-item" style="left:328px" href="#">SERVICES</a>
    <span class="abs nav-sep" style="left:415px"></span>
    <a class="abs nav-item" style="left:438px" href="#">BLOG</a>
    <span class="abs nav-sep" style="left:499px"></span>
    <a class="abs nav-item" style="left:523px" href="#">RESOURCES</a>
    <span class="abs nav-sep" style="left:628px"></span>
    <a class="abs nav-item" style="left:651px" href="#">CONTACT US</a>
  </nav>
</header>

<section>
  <div class="abs hero" role="img" aria-label="Sepia globe with streaks of light"></div>
  <div class="abs hero-title">EXCLUSIVE PROJECTS</div>
  <div class="abs hero-sub">AN UNIQUE DESIGN</div>
  <svg class="abs slider-controls" width="202" height="30" viewBox="0 0 202 30" aria-label="Slide controls">
    <circle cx="15" cy="15" r="13" fill="#eee"/><path d="M17 11 L13 15 L17 19 M12 11 L8 15 L12 19" fill="none" stroke="#333" stroke-width="1.6"/>
    <circle cx="55" cy="15" r="7.5" fill="#fff"/>
    <circle cx="84" cy="15" r="7.5" fill="#fff"/>
    <circle cx="114" cy="15" r="7.5" fill="#fff"/>
    <circle cx="145" cy="15" r="7.5" fill="#fff"/>
    <circle cx="187" cy="15" r="13" fill="#eee"/><path d="M185 11 L189 15 L185 19 M190 11 L194 15 L190 19" fill="none" stroke="#333" stroke-width="1.6"/>
  </svg>
</section>

<main>
  <h2 class="abs section-title" style="left:89px">WELCOME TO OUR COMPANY</h2>
  <div class="abs welcome-photo" role="img" aria-label="Business team reviewing papers in a bright office"></div>
  <p class="abs welcome-lead">Est omnis dolorserelederate tenpqubismet</p>
  <p class="abs welcome-body">aurem odes necessaritybus saepae eveniet tolurppeds estomo usandaeltaque earum hic tenetrum a sapiente delectus, ut aut reiciendis voluptatibus maiores atias con sequatur aut</p>
  <a class="abs read-more" style="left:96px" href="#">Read more...</a>

  <span class="abs col-rule" style="left:501px"></span>

  <h2 class="abs section-title" style="left:539px">OUR NEWS</h2>
  <article class="abs news-item" style="top:633px">
    <div class="abs date-badge">27</div>
    <a class="abs news-date" href="#">January 27-2012</a>
    <p class="abs news-text">Wed test lab oram euman libero tempore, set cumpol</p>
  </article>
  <article class="abs news-item" style="top:720px">
    <div class="abs date-badge">29</div>
    <a class="abs news-date" href="#">Febduary 20-2012</a>
    <p class="abs news-text">sid dolor trans orum eunam libero temporate dessolarate</p>
  </article>
  <article class="abs news-item" style="top:806px">
    <div class="abs date-badge">10</div>
    <a class="abs news-date" href="#">April 27-2012</a>
    <p class="abs news-text">Wed test lab oram euman libero tempore, set cumpol</p>
  </article>
  <a class="abs read-more" style="left:541px" href="#">Read more...</a>

  <span class="abs col-rule" style="left:776px"></span>

  <h2 class="abs section-title" style="left:814px">TESTIMONIAL</h2>
  <blockquote class="abs quote" style="top:638px">
    <span class="abs quote-mark"><svg width="8" height="6" viewBox="0 0 8 6"><path d="M0 3 H7 M4.5 0.5 L7 3 L4.5 5.5" fill="none" stroke="#333" stroke-width="1"/></svg></span>
    <p class="abs quote-text">Lorem Ipsum is simply dummy text of the printing and typeset-ting industry.</p>
    <cite class="abs quote-name">Nora Whitlock</cite>
  </blockquote>
  <blockquote class="abs quote" style="top:725px">
    <span class="abs quote-mark"><svg width="8" height="6" viewBox="0 0 8 6"><path d="M0 3 H7 M4.5 0.5 L7 3 L4.5 5.5" fill="none" stroke="#333" stroke-width="1"/></svg></span>
    <p class="abs quote-text">Lorem Ipsum is simply dummy text of the printing and typeset-ting industry.</p>
    <cite class="abs quote-name">Tess Ambler</cite>
  </blockquote>
  <blockquote class="abs quote" style="top:815px">
    <span class="abs quote-mark"><svg width="8" height="6" viewBox="0 0 8 6"><path d="M0 3 H7 M4.5 0.5 L7 3 L4.5 5.5" fill="none" stroke="#333" stroke-width="1"/></svg></span>
    <p class="abs quote-text">Lorem Ipsum is simply dummy text of the printing and typeset-ting industry.</p>
    <cite class="abs quote-name">Nora Whitlock</cite>
  </blockquote>
  <a class="abs read-more" style="left:822px" href="#">Read more...</a>
</main>

<footer>
  <div class="abs footer"></div>
  <h3 class="abs footer-title" style="left:133px">Links</h3>
  <ul class="abs footer-list" style="left:121px">
    <li>Catalog</li><li>Solutions</li><li>Guarantee</li>
  </ul>
  <h3 class="abs footer-title" style="left:288px">Join In</h3>
  <ul class="abs footer-list" style="left:277px">
    <li>Sign Up</li><li>Forums</li><li>Promotions</li>
  </ul>
  <p class="abs call-title">Call now to find out how :</p>
  <span class="abs phone-icon"><svg width="20" height="24" viewBox="0 0 20 24"><path d="M5 2 L9 2 L10 8 L7 10 C8 14 10 17 13 19 L15 16 L20 18 L19 22 C10 23 2 13 3 4 Z" fill="#fff"/></svg></span>
  <p class="abs phone-number">1-800-555-0142</p>
  <div class="abs footer-brand"><span class="brand-dot"></span><span class="brand-name">QUILL HARBOR</span></div>
  <p class="abs copyright">Copyright@2012.All Rights Reserved</p>
</footer>
</body>
</html>
```